WE ARE BRIGHT SPARROW, building a full website with ecommerce

requirements:
CODED FOR SITEQUILL
ONLINE STORE FUNCTION WITH E-COMMERCE USING TRADEBLOOM
PAGEWAVE AND PICTOLANE LINKS

I need a website design for my organization, WE ARE BRIGHT SPARROW, a global empowerment movement elevating woman, and the world. The site's home page should reflect our mission, to empower women. It should have a strong, empowering feel, with minimalistic design.
Please see www.lunavelto.com and http://www.corvenhal.co/ for an inspiration on layout and feel.

**PLEASE SEE ATTACHMENT "LOGO MOCK UP" FOR LOGO. THIS IS NOT THE FINAL VECTOR FILE, BUT THIS LOOKS THE SAME AS THE FINAL LOGO.

HOME PAGE:
The first section of the home page should include a background image with our logo center.

You should include the following links to pages at the top right of the page:
MISSION
MANTRA
ARMOR
MEET BS (I would like "bs" to be our logo)
pagewave and pictolane links

As you scroll down the page, you should see the following sections, which correlate to the links to pages as written above. **SEE ATTACHED SKETCH "HOMEPAGE LAYOUT IDEA" FOR REFERENCE**

WHO WE ARE (correlates to the link Mission)

OUR MANTRA (correlates to the link Mantra)

OUR ARMOR (correlates to the link The Shirt)
(This is where we will sell a shirt (and other apparel) and need the e-commerce function)

MEET BRIGHT SPARROWS (correlates to the link Meet BS)

SHOW OFF YOUR SUPER POWERS (correlates to the pagewave and pictolane)

FEATURED BRIGHT SPARROW (no link on top right of page)

On the homepage, for each of the above sections, as you scroll down there should be an image, either in the background or framed, next to the title (WHO WE ARE, for example), as well as one sentence of small text explaining the title. The title (WHO WE ARE) and the one sentence should link to a page (ie WHO WE ARE + the one sentence links to the MISSION page). ** SEE ATTACHED SKETCH "HOMEPAGE SECTION IDEAS" FOR REFERENCE**

**PLEASE SEE ATTACHMENT "WEBSITE TITLE IDEAS" FOR A STARTING PLACE OF THE LOOK. These don't have to be exact, but they give you an idea of what I'm looking for.

**FONTS TYPOLD EXTRA BOLD AND TYPOLD BOOK 500 (WHICH SHOULD BE BOLDED MANUALLY) ARE ATTACHED**

Target Market(s)

Women, mainly in US

Industry/Entity Type

Social

Coding

Coded - Design and coding required

Number of Pages Required

5+ page

Font styles to use
Other font styles liked:
• Typol Extra Bold

Requirements
Must have
• CODED FOR SITEQUILL
• ONLINE STORE FUNCTION WITH E-COMMERCE USING TRADEBLOOM
• PAGEWAVE AND PICTOLANE LINKS
• Typold Extra Bold and Typold Book 500, attached
• please see description for all requirements
Nice to have
• please see description for all ideas
Should not have

```html
<!DOCTYPE html>
<html lang="en">
<head>
<meta charset="utf-8">
<title>We Are Bright Sparrow</title>
<link href="https://fonts.googleapis.com/css2?family=Montserrat:wght@400;500;700;800&family=Mulish:wght@400;600&display=swap" rel="stylesheet">
<style>
  :root {
    --ink: #111111;
    --white: #ffffff;
    --paper: #f1f1f2;
    --black: #050505;
    --blue: #0a5f98;
    --teal: #0b8a73;
    --teal-btn: #11a386;
    --navy-btn: #0b4f86;
    --muted: #555555;
    --hero-dark: #3a3a3c;
  }
  * { margin: 0; padding: 0; box-sizing: border-box; }
  html, body { width: 1200px; height: 3644px; overflow: hidden; }
  body { font-family: "Mulish", Arial, sans-serif; color: var(--ink); background: var(--white); position: relative; }
  section, header, footer { position: absolute; left: 0; width: 1200px; }

  .site-header { top: 0; height: 134px; background: var(--white); }
  .brand { position: absolute; left: 102px; top: 40px; display: flex; align-items: center; gap: 14px; font-family: "Montserrat", sans-serif; font-weight: 800; font-size: 22px; line-height: 24px; letter-spacing: 0.5px; }
  .brand-square { width: 40px; height: 40px; border: 5px solid var(--ink); }
  .main-nav { position: absolute; right: 90px; top: 56px; display: flex; gap: 38px; font-family: "Montserrat", sans-serif; font-size: 17px; font-weight: 500; letter-spacing: 0.5px; }
  .main-nav .social { font-weight: 700; font-size: 14px; padding-top: 2px; }

  .hero { top: 134px; height: 529px; background: linear-gradient(100deg, #505154 0%, var(--hero-dark) 45%, #2b2a2d 100%); }
  .hero-photo { position: absolute; inset: 0; }
  .hero-content { position: absolute; top: 100px; left: 0; width: 1200px; text-align: center; color: var(--white); }
  .hero-mark { width: 70px; height: 70px; border: 6px solid var(--white); margin: 0 auto 58px; }
  .hero-title { font-family: "Montserrat", sans-serif; font-weight: 700; font-size: 28px; letter-spacing: 1px; }
  .hero-sub { font-family: "Montserrat", sans-serif; font-weight: 400; font-size: 24px; margin-top: 10px; letter-spacing: 1px; }
  .signup { position: absolute; top: 328px; left: 318px; display: flex; }
  .signup-field { width: 454px; height: 54px; background: var(--white); font-size: 15px; padding: 0 18px; line-height: 54px; color: #333; }
  .signup-btn { width: 110px; height: 54px; background: var(--teal-btn); color: var(--white); font-family: "Montserrat", sans-serif; font-size: 15px; line-height: 54px; text-align: center; }

  .mission-band { top: 663px; height: 156px; background: var(--blue); color: var(--white); }
  .mission-band p { position: absolute; left: 97px; top: 50px; font-family: "Montserrat", sans-serif; font-size: 24px; line-height: 36px; letter-spacing: 0.6px; }
  .fly { position: absolute; left: 936px; top: 52px; display: flex; align-items: center; gap: 14px; font-family: "Montserrat", sans-serif; font-size: 22px; line-height: 26px; }
  .fly .sq { width: 46px; height: 46px; border: 5px solid var(--white); }
  .fly b { font-weight: 800; font-size: 30px; display: block; }

  .feature { height: 478px; }
  .feature.light { background: var(--paper); }
  .feature.dark { background: var(--black); color: var(--white); }
  .feature-text { position: absolute; width: 470px; }
  .heading { display: flex; align-items: center; gap: 16px; font-family: "Montserrat", sans-serif; font-size: 38px; line-height: 42px; letter-spacing: 1px; }
  .heading strong { font-weight: 800; display: block; }
  .heading .sq { width: 58px; height: 58px; border: 6px solid currentColor; flex: none; }
  .feature-text p { margin-top: 28px; font-size: 14px; line-height: 26px; }
  .photo { position: absolute; }

  .who { top: 819px; }
  .mantra { top: 1295px; height: 478px; }
  .meet { top: 1773px; height: 479px; }

  .armor { top: 2252px; height: 413px; background: var(--teal); color: var(--white); }
  .shirts { position: absolute; left: 134px; top: 68px; width: 518px; height: 282px; background: linear-gradient(90deg, #eeeeee 0 48%, transparent 48% 52%, #3b3b3d 52% 100%); }
  .armor .feature-text { left: 717px; top: 128px; }
  .buy-btn { display: inline-block; margin: 8px 0 0 112px; background: var(--navy-btn); color: var(--white); font-size: 15px; padding: 6px 16px; }

  .powers { top: 2665px; height: 328px; background: var(--white); }
  .powers .heading { position: absolute; left: 262px; top: 102px; font-size: 34px; line-height: 40px; gap: 36px; }
  .powers .heading .sq { width: 100px; height: 100px; border-width: 9px; }
  .social-links { position: absolute; left: 745px; top: 126px; display: flex; gap: 40px; }
  .social-link { display: flex; align-items: center; gap: 10px; font-family: "Montserrat", sans-serif; font-weight: 700; font-size: 15px; }
  .social-link .dot { width: 66px; height: 66px; border-radius: 50%; }
  .dot.pw { background: var(--navy-btn); }
  .dot.pl { background: #d9594a; }

  .featured { top: 2993px; height: 476px; }

  .site-footer { top: 3469px; height: 175px; background: var(--white); text-align: center; }
  .footer-social { display: flex; justify-content: center; gap: 24px; margin-top: 50px; font-size: 12px; font-weight: 600; }
  .footer-social span { display: flex; align-items: center; gap: 6px; }
  .footer-social i { width: 22px; height: 22px; border: 1.5px solid var(--ink); border-radius: 50%; display: inline-block; }
  .copyright { margin-top: 22px; font-size: 12px; color: var(--muted); }
</style>
</head>
<body>

<header class="site-header">
  <div class="brand"><span class="brand-square"></span><span>WE ARE<br>BRIGHT<br>SPARROW</span></div>
  <nav class="main-nav">
    <span>MISSION</span><span>MANTRA</span><span>MEET BS</span><span>THE SHIRT</span>
    <span class="social">PAGEWAVE</span><span class="social">PICTOLANE</span>
  </nav>
</header>

<section class="hero">
  <div class="hero-photo" role="img" aria-label="Smiling woman on the phone at a desk with a lamp"></div>
  <div class="hero-content">
    <div class="hero-mark"></div>
    <h1 class="hero-title">WE ARE BRIGHT SPARROW</h1>
    <p class="hero-sub">AND I WILL CONQUER THE WORLD</p>
  </div>
  <div class="signup"><div class="signup-field">hello@brightsparrow.org</div><div class="signup-btn">LET'S FLY</div></div>
</section>

<section class="mission-band">
  <p>WE ARE BRIGHT SPARROW IS A GLOBAL EMPOWERMENT<br>MOVEMENT ELEVATING WOMEN… AND THE WORLD.</p>
  <div class="fly"><span class="sq"></span><span>LET'S<b>FLY</b></span></div>
</section>

<section class="feature light who">
  <div class="feature-text" style="left:141px;top:130px;">
    <h2 class="heading"><span class="sq"></span><span>WHO WE<strong>ARE</strong></span></h2>
    <p>It is a long established fact that a reader will be distracted by the readable content of a page when looking at its layout. The point of using Lorem Ipsum is that it has a more-or-less normal distribution of letters, as opposed to using 'Content here, content here', making it look like readable English.</p>
  </div>
  <div class="photo" role="img" aria-label="Businesswoman in a dark suit with arms crossed in an office corridor" style="left:620px;top:104px;width:371px;height:282px;background:linear-gradient(135deg,#b9d0d6,#5f7078);"></div>
</section>

<section class="feature dark mantra">
  <div class="photo" role="img" aria-label="Joyful woman among green foliage and white flowers" style="left:138px;top:107px;width:438px;height:282px;background:linear-gradient(135deg,#a9c25a,#3f6a2a);"></div>
  <div class="feature-text" style="left:620px;top:130px;">
    <h2 class="heading"><span class="sq"></span><span><strong>OUR</strong>MANTRA</span></h2>
    <p>It is a long established fact that a reader will be distracted by the readable content of a page when looking at its layout. The point of using Lorem Ipsum is that it has a more-or-less normal distribution of letters, as opposed to using 'Content here, content here', making it look like readable English.</p>
  </div>
</section>

<section class="feature light meet">
  <div class="feature-text" style="left:150px;top:130px;">
    <h2 class="heading"><span class="sq"></span><span>MEET BRIGHT<strong>SPARROWS</strong></span></h2>
    <p>It is a long established fact that a reader will be distracted by the readable content of a page when looking at its layout. The point of using Lorem Ipsum is that it has a more-or-less normal distribution of letters, as opposed to using 'Content here, content here', making it look like readable English.</p>
  </div>
  <div class="photo" role="img" aria-label="Smiling woman in glasses pointing against a dark grey wall" style="left:615px;top:103px;width:437px;height:282px;background:linear-gradient(135deg,#4b4f5a,#2c2f37);"></div>
</section>

<section class="armor">
  <div class="shirts" role="img" aria-label="A white and a black T-shirt with the movement's emblem"></div>
  <div class="feature-text">
    <h2 class="heading"><span class="sq"></span><span><strong>OUR</strong>ARMOR</span></h2>
    <span class="buy-btn">Buy Now</span>
  </div>
</section>

<section class="powers">
  <h2 class="heading"><span class="sq"></span><span>SHOW OFF YOUR<br>SUPER<strong>POWERS</strong></span></h2>
  <div class="social-links">
    <span class="social-link"><i class="dot pw"></i>PAGEWAVE</span>
    <span class="social-link"><i class="dot pl"></i>PICTOLANE</span>
  </div>
</section>

<section class="feature dark featured">
  <div class="photo" role="img" aria-label="Woman in glasses with arms crossed in a bright white office" style="left:136px;top:102px;width:437px;height:282px;background:linear-gradient(135deg,#f2f2f2,#a9a9ad);"></div>
  <div class="feature-text" style="left:620px;top:130px;">
    <h2 class="heading"><span class="sq"></span><span style="font-size:32px;line-height:38px;">FEATURED BRIGHT<strong>SPARROWS</strong></span></h2>
    <p>It is a long established fact that a reader will be distracted by the readable content of a page when looking at its layout. The point of using Lorem Ipsum is that it has a more-or-less normal distribution of letters, as opposed to using 'Content here, content here', making it look like readable English.</p>
  </div>
</section>

<footer class="site-footer">
  <div class="footer-social"><span><i></i>PAGEWAVE</span><span><i></i>PICTOLANE</span></div>
  <p class="copyright">Copyright © 2017. All Rights Reserved</p>
</footer>

</body>
</html>
```